Payment company requires web design

We need a web design for a new company based in Singapore.

The company focuses on providing 2 key products: 1) an alternative payment option (i.e. like quib or trelloquin options) on the traditional checkout process 2) a replacement/outsource of a merchants payment page. Key in the UX flow is a end customer dashboard that manages all payments.

We look to provide a simple, fluid and easy to use payment process. The dashboard is minimalistic that allows easy navigation, review of transactions and all available options through gamification.

The final design should communicate ease of use, flexibility and transparency.

Target Market(s)

The value is for the merchant - retail/travel/insurance companies. However its the merchant's end customers that are the target and who the UX is built for.

Industry/Entity Type

It Company

Logo Text

zelnar

Number of Pages Required

5+ page

Colors
ec1f27

Requirements
Must have
• 7 pages mimicking UX flow
• payment page * 2 - 1) alternative payment type 2) outsource of merchants payment page to our business
• our landing page
• end customer verification page
• end customer registration
• customer dashboard
• UX flow in attached file
Nice to have
• open to ideas
• have asked for the logo to be added
• logo to have the colour red (chinese for prosperity)
• the company is all about flexibility, transparency in personal finance management with the option of instalment payments

```html
<!DOCTYPE html>
<html lang="en">
<head>
<meta charset="utf-8">
<title>Zelnar</title>
<link href="https://fonts.googleapis.com/css2?family=Roboto:wght@400;500;700&family=Arimo:wght@400;700&display=swap" rel="stylesheet">
<style>
:root{
  --red:#ec1f27;
  --red-soft:#ef4b50;
  --ink:#333333;
  --text:#666666;
  --muted:#999999;
  --grey-btn:#5a5a5a;
  --light:#f4f4f4;
  --line:#e6e6e6;
  --white:#ffffff;
}
*{margin:0;padding:0;box-sizing:border-box}
html,body{width:1200px;height:2182px;overflow:hidden;background:var(--white)}
body{position:relative;font-family:"Arimo",Arial,sans-serif;color:var(--text)}
.abs{position:absolute}
.heading{font-family:"Roboto",Arial,sans-serif;font-weight:400;color:var(--ink)}

/* header */
.site-header{left:0;top:0;width:1200px;height:95px;border-bottom:1px solid var(--line);background:var(--white)}
.brand{left:87px;top:28px;display:flex;align-items:center;gap:12px}
.brand-mark{width:36px;height:36px;border-radius:50%;background:var(--red)}
.brand-name{font-family:"Roboto",sans-serif;font-weight:500;font-size:32px;color:var(--red);letter-spacing:0.5px}
.main-nav{right:86px;top:42px;display:flex;gap:40px;font-family:"Roboto",sans-serif;font-size:12px;color:var(--ink)}
.main-nav .active{color:var(--red)}

/* hero */
.hero{left:0;top:95px;width:1200px;height:487px;background:linear-gradient(90deg,#f3f4f2 0%,#eef0ee 38%,#d9dcd8 52%,#c9b8a6 70%,#d7c6b4 85%,#ece9e4 100%)}
.hero-photo{left:470px;top:0;width:730px;height:487px;background:radial-gradient(ellipse at 60% 45%,rgba(196,150,120,0.55),rgba(230,228,222,0) 70%)}
.hero-title{left:87px;top:130px;font-family:"Roboto",sans-serif;font-weight:500;font-size:32px;color:var(--red)}
.hero-sub{left:87px;top:178px;font-family:"Arimo",sans-serif;font-weight:700;font-size:15.5px;color:#444}
.hero-text{left:87px;top:208px;width:420px;font-size:12.5px;line-height:27px;color:var(--text)}
.btn{display:flex;align-items:center;justify-content:center;font-family:"Roboto",sans-serif;font-weight:500;font-size:15px;color:var(--white);border-radius:3px}
.btn-buy{left:87px;top:404px;width:109px;height:38px;background:var(--red)}
.btn-register{left:202px;top:404px;width:109px;height:38px;background:var(--grey-btn)}
.slider-dots{left:87px;top:556px;display:flex;gap:8px}
.slider-dots span{width:10px;height:10px;border-radius:50%;background:#777}
.slider-dots .on{background:var(--red)}

/* services */
.section-title{width:1200px;left:0;text-align:center;font-size:21px}
.section-lead{width:1200px;left:0;text-align:center;font-size:12.5px;color:var(--muted)}
.service-icon{width:104px;height:104px;border-radius:50%;background:var(--red);border:3px solid var(--white);box-shadow:0 0 0 2px #555;display:flex;align-items:center;justify-content:center}
.service-name{width:320px;text-align:center;font-family:"Roboto",sans-serif;font-weight:500;font-size:15px;color:var(--red)}
.service-text{width:300px;text-align:center;font-size:12px;line-height:23.5px;color:var(--text)}

/* welcome */
.welcome-panel{left:0;top:993px;width:600px;height:348px}
.welcome-art{left:90px;top:1010px;width:380px;height:320px;border-radius:8px;background:linear-gradient(135deg,#3a3a3a 0%,#6a7c8c 40%,#4aa3c8 60%,#d6c56a 80%,#e9e9e9 100%);opacity:0.85}
.welcome-title{left:604px;top:1028px;font-size:21px}
.welcome-text{left:604px;top:1080px;width:512px;font-size:12px;line-height:24px;color:var(--text)}
.read-more{left:604px;top:1286px;font-family:"Roboto",sans-serif;font-weight:700;font-size:12px;color:var(--red);text-decoration:underline}

/* featured */
.featured{left:0;top:1341px;width:1200px;height:290px;background:linear-gradient(90deg,#e8373d 0%,#ef4b50 45%,#f06166 75%,#ea3d43 100%)}
.featured-title{left:0;top:1396px;width:1200px;text-align:center;font-family:"Roboto",sans-serif;font-weight:500;font-size:21px;color:var(--white)}
.featured-text{left:260px;top:1438px;width:680px;text-align:center;font-size:12px;line-height:24px;color:var(--white)}
.btn-outline{left:481px;top:1537px;width:238px;height:41px;border:1px solid var(--white);border-radius:2px;color:var(--white);font-family:"Roboto",sans-serif;font-size:12px;display:flex;align-items:center;justify-content:center}

/* newsletter & pay */
.signup-band{left:0;top:1631px;width:1200px;height:312px;border-bottom:1px solid var(--line)}
.block-title{font-size:22px}
.block-title em{font-style:normal;font-weight:500;color:var(--red)}
.block-text{font-size:12px;line-height:22px;color:var(--text)}
.email-field{left:87px;top:1805px;width:441px;height:45px;background:#f7f7f7;border:1px solid #e9e9e9;border-radius:2px;padding:0 18px;display:flex;align-items:center;font-size:12.5px;color:#444}
.btn-submit{left:87px;top:1868px;width:122px;height:40px;background:var(--red);font-size:14px}
.methods{left:688px;top:1827px;width:406px;height:58px;background:var(--white);border:1px solid #d9d9d9;display:flex;align-items:center;gap:10px;padding:0 12px}
.methods-label{font-family:"Roboto",sans-serif;font-style:italic;font-size:13.5px;color:#555;margin-right:6px}
.card-chip{height:24px;padding:0 6px;border:1px solid #ccc;border-radius:2px;display:flex;align-items:center;font-family:"Roboto",sans-serif;font-weight:500;font-size:10px;color:#444;background:var(--white)}

/* footer */
.social{top:1987px;width:60px;height:60px;border-radius:50%;border:1px solid #d6d6d6;display:flex;align-items:center;justify-content:center;font-family:"Roboto",sans-serif;font-size:10px;color:#888}
.footer-rule{left:84px;top:2067px;width:1033px;height:1px;background:var(--line)}
.footer-nav{left:0;top:2095px;width:1200px;display:flex;justify-content:center;gap:20px;font-family:"Roboto",sans-serif;font-size:11.5px;color:var(--muted)}
.copyright{left:0;top:2137px;width:1200px;text-align:center;font-size:11px;color:var(--muted)}
.bottom-bar{left:0;top:2178px;width:1200px;height:4px;background:#777}
</style>
</head>
<body>

<header class="abs site-header">
  <div class="abs brand"><span class="brand-mark"></span><span class="brand-name">ZELNAR</span></div>
  <nav class="abs main-nav">
    <span class="active">HOME</span><span>ABOUT US</span><span>SERVICES</span><span>NEWS</span><span>TESTIMONIALS</span><span>CONTACT US</span>
  </nav>
</header>

<section class="abs hero">
  <div class="abs hero-photo" role="img" aria-label="Photo of a smiling couple shopping online at a laptop, holding a payment card"></div>
</section>
<h1 class="abs hero-title">ZELNAR</h1>
<p class="abs hero-sub">NEQUE PORRO QUISQUAM EST QUI DOLOREM IPSUM</p>
<p class="abs hero-text">Sed ut perspiciatis unde omnis iste natus error sit voluptatem accusanti um doloremque laudantium, totam rem aperiam, eaque ipsa quae ab et quasi architecto beatae vitae dicta sunt explicabo.</p>
<a class="abs btn btn-buy">BUY NOW</a>
<a class="abs btn btn-register">REGISTER</a>
<div class="abs slider-dots"><span></span><span class="on"></span><span></span></div>

<h2 class="abs heading section-title" style="top:623px">OUR SERVICE</h2>
<p class="abs section-lead" style="top:662px">Sed ut perspiciatis unde omnis iste natus error sit voluptatem accusantium doloremque laudantium</p>

<div class="abs service-icon" style="left:197px;top:709px">
  <svg width="52" height="52" viewBox="0 0 52 52" fill="none" stroke="#fff" stroke-width="5" stroke-linecap="round" stroke-linejoin="round"><path d="M26 48V28M26 28L12 14M26 28L40 14M6 16V8h8M46 16V8h-8M26 12V4M21 9l5-5 5 5"/></svg>
</div>
<div class="abs service-icon" style="left:547px;top:709px">
  <svg width="52" height="52" viewBox="0 0 52 52" fill="none" stroke="#fff" stroke-width="5" stroke-linecap="round"><circle cx="22" cy="22" r="15"/><circle cx="22" cy="22" r="6"/><path d="M33 33l13 13"/></svg>
</div>
<div class="abs service-icon" style="left:883px;top:709px">
  <svg width="52" height="52" viewBox="0 0 52 52" fill="#fff"><circle cx="18" cy="10" r="7"/><path d="M6 48V26a8 8 0 0 1 8-8h8a8 8 0 0 1 8 8v22z"/><rect x="32" y="24" width="16" height="18" rx="5"/></svg>
</div>
<svg class="abs" style="left:365px;top:735px" width="110" height="50" viewBox="0 0 110 50" fill="none" stroke="#f6c9cb" stroke-width="8" stroke-linecap="round"><path d="M6 38C30 12 70 12 96 30"/><path d="M82 16l16 14-18 8"/></svg>
<svg class="abs" style="left:710px;top:735px" width="110" height="50" viewBox="0 0 110 50" fill="none" stroke="#f6c9cb" stroke-width="8" stroke-linecap="round"><path d="M6 18C30 44 70 44 98 16"/><path d="M82 12l16 4-4 18"/></svg>

<h3 class="abs service-name" style="left:89px;top:836px">FLEXIBILITY</h3>
<h3 class="abs service-name" style="left:439px;top:836px">TRANSPARENCY</h3>
<h3 class="abs service-name" style="left:775px;top:836px">FINANCE MANAGEMENT</h3>
<p class="abs service-text" style="left:99px;top:864px">Sed ut perspiciatis unde omnis iste natus error sit voluptatem accusantium doloremque laud antium atae vitae dicta sunt explicabo.</p>
<p class="abs service-text" style="left:449px;top:864px">Sed ut perspiciatis unde omnis iste natus error sit voluptatem accusantium doloremque laud antium atae vitae dicta sunt explicabo.</p>
<p class="abs service-text" style="left:785px;top:864px">Sed ut perspiciatis unde omnis iste natus error sit voluptatem accusantium doloremque laud antium atae vitae dicta sunt explicabo.</p>

<svg class="abs welcome-panel" width="600" height="348" viewBox="0 0 600 348"><polygon points="0,0 472,0 589,348 0,348" fill="#f3f4f5"/><line x1="472" y1="0" x2="589" y2="348" stroke="#e2e2e2"/></svg>
<div class="abs welcome-art" role="img" aria-label="Illustration of a laptop with bank cards and a computer mouse"></div>
<h2 class="abs heading welcome-title">WELCOME TO ZELNAR</h2>
<div class="abs welcome-text">
  <p>Sed ut perspiciatis unde omnis iste natus error sit voluptatem accusantium doloremque laud antium, totam rem aperiam, eaque ipsa quae ab illo inventore veritatis et quasi architecto be atae vitae dicta sunt explicabo. Nemo enim ipsam voluptatem quia voluptas sit aspernatur aut magni dolores eos qui ratione voluptatem sequi nesciunt.</p>
  <p style="margin-top:20px">Sed ut perspiciatis unde omnis iste natus error sit voluptatem accusantium doloremque lauda n ium, totam rem aperiam, eaque ipsa quae ab illo inventore veritatis et quasi architecto aut odit aut fugit, sed quia consequuntur magni dolores eos qui ratione voluptatem</p>
</div>
<a class="abs read-more">READ MORE</a>

<section class="abs featured" role="img" aria-label="Red-tinted photo of hands paying by card at a laptop"></section>
<h2 class="abs featured-title">OUR FEATURED</h2>
<p class="abs featured-text">Sed ut perspiciatis unde omnis iste natus error sit voluptatem accusantium doloremque laud antium, totam rem aperiam, eaque ipsa quae ab illo inventore veritatis et quasi architecto be atae vitae dicta sunt explicabo. Nemo enim aut magni quasi architecto beatae dolores eos qui ratione voluptatem sequi nesciunt.</p>
<a class="abs btn-outline">CLICK HERE FOR MORE INFO</a>

<svg class="abs signup-band" width="1200" height="312" viewBox="0 0 1200 312"><rect width="1200" height="312" fill="#f4f4f4"/><polygon points="0,0 560,0 625,312 0,312" fill="#fff"/></svg>
<h2 class="abs heading block-title" style="left:87px;top:1694px">NEWSLETTER <em>SIGNUP</em></h2>
<p class="abs block-text" style="left:87px;top:1745px;width:450px">Sed ut perspiciatis unde omnis iste natus error sit voluptatem accusantium et quasi architecto beatae vitae dicta sunt explicabo.</p>
<div class="abs email-field">Enter your email id :</div>
<a class="abs btn btn-submit">SUBMIT NOW</a>

<h2 class="abs heading block-title" style="left:688px;top:1694px">PAY <em>WITH</em></h2>
<p class="abs block-text" style="left:688px;top:1740px;width:420px">Sed ut perspiciatis unde omnis iste natus error sit voluptatem accusantium doloremque laudantium, totam rem aperiam, eaque ipsa quae ab illo inventore veritatis et quasi architecto beatae vitae dicta sunt explicabo.</p>
<div class="abs methods">
  <span class="methods-label">Payment Methods:</span>
  <span class="card-chip">QUIB</span><span class="card-chip">TRELLOQUIN</span><span class="card-chip">CENTRIX</span><span class="card-chip">DOVEX</span><span class="card-chip">PAYVO</span>
</div>

<a class="abs social" style="left:387px">Folio</a>
<a class="abs social" style="left:460px">Chirpa</a>
<a class="abs social" style="left:531px">Orbi</a>
<a class="abs social" style="left:603px">Netwo</a>
<a class="abs social" style="left:674px">Pixo</a>
<a class="abs social" style="left:747px"><svg width="18" height="14" viewBox="0 0 18 14" fill="none" stroke="#888" stroke-width="1.6"><rect x="1" y="1" width="16" height="12" rx="1"/><path d="M1 2l8 6 8-6"/></svg></a>
<div class="abs footer-rule"></div>
<nav class="abs footer-nav"><span>HOME</span><span>|</span><span>ABOUT US</span><span>|</span><span>SERVICES</span><span>|</span><span>NEWS</span><span>|</span><span>TESTIMONIALS</span><span>|</span><span>CONTACT US</span></nav>
<p class="abs copyright">© Copyrights 2016 Zelnar.ll Rights Reserved.</p>
<div class="abs bottom-bar"></div>

</body>
</html>
```